Ledgerwise Forge - WordPress Theme & Logo

Design a logo and Wordpress website design for Ledgerwise Forge. Ledgerwise Forge provides cryptocurrency development services to clients who need a team to create & continue developing a new cryptocurrency or who want to replace their current cryptocurrency development team. more details in the attached document.
Updates

Target Market(s)

Entrepreneurs who are building a business / platform that makes use of an underlying cryptocurrency.

Logo Text

LF or Ledgerwise Forge

Coding

Coded - Design and coding required

Font styles to use
Sans Serif

Requirements
Must have
• Professional logo, complete coded Wordpress theme for all pages, containing all specified links and buttons
Nice to have
• It would be nice if the buttons that are meant to integrate with Dealtrail contain the necessary code for that. I can provide any necessary Dealtrail details from my account.
Should not have
• Slow loading time

```html
<!DOCTYPE html>
<html lang="en">
<head>
<meta charset="utf-8">
<title>Ledgerwise Forge</title>
<link href="https://fonts.googleapis.com/css2?family=Roboto:wght@300;400;500;700;900&display=swap" rel="stylesheet">
<style>
:root{
  --blue:#0d5cb6;
  --blue-dark:#0a4a96;
  --navy:#071630;
  --ink:#1b1b1b;
  --text:#3a3a3a;
  --muted:#8a8f98;
  --pale:#eaf2fb;
  --white:#ffffff;
}
*{box-sizing:border-box;margin:0;padding:0}
html,body{width:1200px;height:4026px;overflow:hidden}
body{font-family:'Roboto',sans-serif;color:var(--text);background:var(--white);position:relative}
a{color:inherit;text-decoration:none}
.topline{height:6px;background:var(--blue)}
.header{height:99px;position:relative}
.brand{position:absolute;left:110px;top:22px;display:flex;align-items:center;gap:10px}
.brand-mark{width:46px;height:46px;border-radius:50%;background:var(--blue)}
.brand-name{font-weight:700;font-size:16px;line-height:19px;color:var(--ink);text-transform:uppercase}
.contact{position:absolute;top:30px;display:flex;gap:14px;align-items:flex-start}
.contact svg{width:36px;height:36px}
.contact b{display:block;font-size:14px;font-weight:500;color:var(--ink);margin-bottom:6px}
.contact span{font-size:15px;color:#444}
.nav{height:55px;background:var(--blue);position:relative;display:flex;align-items:center}
.nav ul{list-style:none;display:flex;padding-left:60px}
.nav li{color:#fff;font-weight:700;font-size:15px;margin-right:42px}
.search{position:absolute;right:0;top:0;width:270px;height:55px;background:var(--blue-dark);clip-path:polygon(18px 0,100% 0,100% 100%,0 100%)}
.search::before{content:"";position:absolute;left:6px;top:0;width:6px;height:55px;background:#fff;transform:skewX(-20px)}
.search-field{position:absolute;left:30px;top:8px;right:14px;height:38px;background:#0a3f85;color:#fff;font-size:15px;font-weight:500;padding:11px 12px}
.search-btn{position:absolute;right:6px;top:6px;width:26px;height:26px;background:var(--blue);display:flex;align-items:center;justify-content:center}
.hero{height:613px;position:relative;background:var(--blue);clip-path:polygon(0 0,100% 0,100% 86%,50% 100%,0 86%)}
.hero-image{position:absolute;inset:0;background:radial-gradient(ellipse at 50% 55%,#1e5fa6 0%,#123a6c 35%,#0a1f3d 75%);clip-path:polygon(0 0,100% 0,100% 83%,50% 95%,0 83%)}
.hero h1{position:absolute;top:148px;width:100%;text-align:center;color:#fff;font-size:50px;font-weight:700}
.hero p{position:absolute;top:237px;width:100%;text-align:center;color:#fff;font-size:21px;font-weight:300}
.hero-actions{position:absolute;top:310px;width:100%;display:flex;justify-content:center;gap:16px}
.btn{display:inline-flex;align-items:center;gap:10px;background:var(--blue);color:#fff;font-weight:700;font-size:15px;text-transform:uppercase;padding:0 20px;height:45px}
.btn i{width:13px;height:13px;border-radius:50%;background:#fff;position:relative}
.btn i::after{content:"";position:absolute;left:3px;top:3.5px;border-left:6px solid var(--blue);border-top:3px solid transparent;border-bottom:3px solid transparent}
.arrow-round{position:absolute;top:240px;width:36px;height:36px;border-radius:50%;background:var(--blue);display:flex;align-items:center;justify-content:center}
.section-title{text-align:center;font-size:38px;font-weight:700;color:var(--ink);text-transform:uppercase}
.section-title::after{content:"";display:block;width:66px;height:4px;background:var(--blue);margin:18px auto 0}
.welcome{height:402px;text-align:center;padding-top:78px}
.welcome p{width:700px;margin:36px auto 34px;font-size:15px;line-height:26px}
.why{height:495px;background:linear-gradient(135deg,#0b4ea0,#1266c4 55%,#0c56ad);padding-top:62px}
.why .section-title{color:#fff}
.why .section-title::after{background:#fff}
.feature-row{display:flex;justify-content:center;gap:35px;margin-top:52px}
.feature{width:265px;height:248px;background:#fff;text-align:center;padding-top:28px}
.feature svg{width:110px;height:95px}
.feature h3{font-size:16px;font-weight:700;color:var(--ink);margin-top:22px}
.feature p{font-size:15px;line-height:21px;margin:14px auto 0;width:200px}
.about{height:478px;position:relative}
.about-photo{position:absolute;left:133px;top:70px;width:326px;height:320px;background:linear-gradient(120deg,#1b3550,#6d8aa3 50%,#c4d0d8);box-shadow:10px 10px 0 var(--blue)}
.about h2{position:absolute;left:559px;top:74px;font-size:38px;font-weight:700;color:var(--ink)}
.about p{position:absolute;left:559px;top:152px;width:520px;font-size:15px;line-height:30px}
.about .btn{position:absolute;left:559px;top:361px}
.testimonials{height:482px;background:linear-gradient(180deg,#0c59b3,#0e5fbb 60%,#0a4f9f);position:relative;padding-top:36px}
.testimonials .section-title{color:#fff}
.testimonials .section-title::after{background:#fff}
.review{position:absolute;background:#fff;text-align:center}
.review .avatar{position:absolute;left:50%;transform:translateX(-50%);border-radius:50%;background:linear-gradient(#b9c6d4,#6f8196);border:4px solid #fff}
.review h4{color:var(--blue);font-weight:700}
.review .lead{color:#333}
.review .body{color:var(--muted);font-weight:300}
.carousel-arrow{position:absolute;top:297px}
.services{height:628px;padding-top:90px}
.service-row{position:relative;height:360px;margin-top:44px}
.service{position:absolute;width:282px;height:356px;background:#fff;box-shadow:0 0 10px rgba(0,0,0,.12);text-align:center;padding-top:26px}
.service svg{width:120px;height:120px}
.service h3{font-size:15px;font-weight:700;color:var(--ink);margin-top:20px}
.service ul{list-style:none;text-align:left;margin:16px 0 0 42px}
.service li{font-size:15px;color:#444;line-height:35px;display:flex;align-items:center;gap:10px}
.service li::before{content:"";width:12px;height:12px;border-radius:50%;background:var(--blue);flex:none}
.service .more{display:inline-block;margin-top:10px;color:var(--blue);font-weight:700;font-size:15px}
.promo{height:367px;background:var(--pale);text-align:center;padding-top:48px}
.promo p{width:750px;margin:30px auto 34px;font-size:15px;line-height:26px}
.footer{height:401px;background:var(--pale);position:relative}
.footer-edge{position:absolute;inset:0;background:var(--blue);clip-path:polygon(0 90px,50% 0,100% 90px,100% 100%,0 100%)}
.footer-body{position:absolute;inset:0;background:linear-gradient(180deg,#0a1a36,#040b18);clip-path:polygon(0 98px,50% 10px,100% 98px,100% 100%,0 100%);color:#fff}
.footer-brand{position:absolute;left:106px;top:117px;display:flex;align-items:center;gap:10px}
.footer-brand .brand-name{color:#fff}
.footer-about{position:absolute;left:106px;top:197px;width:260px;font-size:16px;line-height:24px}
.footer-col{position:absolute;top:109px}
.footer-col h5{font-size:19px;font-weight:400;margin-bottom:18px}
.footer-col li{list-style:none;font-size:15px;line-height:34px}
.newsletter{position:absolute;left:878px;top:112px}
.newsletter h5{font-size:15px;font-weight:500;margin-bottom:16px}
.newsletter .field{width:207px;height:40px;background:#fff;color:#555;font-size:13px;padding:12px}
.newsletter .btn{margin-top:16px;height:38px;font-size:15px;padding:0 24px}
.social{display:flex;gap:24px;margin-top:24px}
.social span{width:10px;height:10px;border-radius:50%;background:#fff}
.footer-rule{position:absolute;left:106px;right:116px;top:336px;height:1px;background:#3b4a66}
.copyright{position:absolute;top:361px;width:100%;text-align:center;font-size:15px}
</style>
</head>
<body>
<div class="topline"></div>
<header class="header">
  <div class="brand"><div class="brand-mark"></div><div class="brand-name">Ledgerwise<br>Forge</div></div>
  <div class="contact" style="left:618px">
    <svg viewBox="0 0 36 36"><circle cx="18" cy="18" r="16" fill="none" stroke="#0d5cb6" stroke-width="2"/><path d="M12 11c2-2 3 0 4 2s-1 2-1 3 3 5 5 5 1-2 3-1 3 2 1 4-8 0-11-4-3-7-1-9z" fill="#0d5cb6"/></svg>
    <div><b>Phone</b><span>123 (4570) 612</span></div>
  </div>
  <div class="contact" style="left:832px">
    <svg viewBox="0 0 36 36"><rect x="3" y="9" width="30" height="20" fill="none" stroke="#0d5cb6" stroke-width="2"/><path d="M3 9l15 12 15-12" fill="none" stroke="#0d5cb6" stroke-width="2"/></svg>
    <div><b>Email</b><span>info@ledgerwiseforge.com</span></div>
  </div>
</header>
<nav class="nav">
  <ul><li>Home</li><li>Services</li><li>About Us</li><li>Ledgerwise Forge Method</li><li>Testimonials</li><li>Blog</li><li>Contact Us</li></ul>
  <div class="search"><div class="search-field">Search</div>
    <div class="search-btn" style="top:14px;right:20px"><svg width="14" height="14" viewBox="0 0 14 14"><circle cx="6" cy="6" r="4" fill="none" stroke="#fff" stroke-width="2"/><path d="M9 9l4 4" stroke="#fff" stroke-width="2"/></svg></div>
  </div>
</nav>
<section class="hero">
  <div class="hero-image" role="img" aria-label="Person standing before a glowing city skyline overlaid with a network of connected nodes"></div>
  <div class="arrow-round" style="left:30px"><svg width="14" height="14" viewBox="0 0 14 14"><path d="M9 2L4 7l5 5" fill="none" stroke="#fff" stroke-width="2.5"/></svg></div>
  <div class="arrow-round" style="right:30px"><svg width="14" height="14" viewBox="0 0 14 14"><path d="M5 2l5 5-5 5" fill="none" stroke="#fff" stroke-width="2.5"/></svg></div>
  <h1>LEDGERWISE FORGE</h1>
  <p>Your own cryptocurrency. Secure, easy to use, and built by an expert team.</p>
  <div class="hero-actions"><a class="btn">Get Stared <i></i></a><a class="btn">Schedule Free Consultation <i></i></a></div>
</section>
<section class="welcome">
  <h2 class="section-title">Welcome To</h2>
  <p>Ledgerwise Forge adds professionalism to cryptocurrency development. Our done-for-you service covers everything from development and IT operations to ongoing support. You have access to a full team, for less than the typical cost of a single developer.</p>
  <a class="btn">Learn More <i></i></a>
</section>
<section class="why">
  <h2 class="section-title">Why Choose Ledgerwise Forge</h2>
  <div class="feature-row">
    <div class="feature">
      <svg viewBox="0 0 110 95"><path d="M40 5h50l20 45-20 45H40z" fill="#e8f0fa"/><circle cx="45" cy="25" r="10" fill="#0d5cb6"/><path d="M32 38h26v16H32z" fill="#0d5cb6"/><path d="M12 45l14 20h38l14-20-10 30H22z" fill="#0d5cb6"/></svg>
      <h3>VALUE</h3><p>A team of experts, regular updates, and fixed costs</p>
    </div>
    <div class="feature">
      <svg viewBox="0 0 110 95"><path d="M40 5h50l20 45-20 45H40z" fill="#e8f0fa"/><circle cx="40" cy="32" r="14" fill="none" stroke="#0d5cb6" stroke-width="4"/><circle cx="66" cy="26" r="13" fill="none" stroke="#0d5cb6" stroke-width="4"/><rect x="26" y="52" width="50" height="28" fill="#0d5cb6"/></svg>
      <h3>SUPPORT</h3><p>Receive advice and other services, beyond development.</p>
    </div>
    <div class="feature">
      <svg viewBox="0 0 110 95"><path d="M40 5h50l20 45-20 45H40z" fill="#e8f0fa"/><circle cx="52" cy="30" r="20" fill="#0d5cb6"/><rect x="20" y="52" width="14" height="26" fill="#0d5cb6"/><rect x="72" y="52" width="14" height="26" fill="#0d5cb6"/><path d="M34 56h38v14H34z" fill="#0d5cb6"/></svg>
      <h3>COMMITMENT</h3><p>Enjoy regular updates and new features.</p>
    </div>
  </div>
</section>
<section class="about">
  <div class="about-photo" role="img" aria-label="Two colleagues reviewing a tablet in a server room"></div>
  <h2>ABOUT US</h2>
  <p>In addition to creating and enhancing cryptocurrencies for clients, the Ledgerwise Forge team has been running the Tessel cryptocurrency since 2017. We prefer long-term relationships, enabling us to deliver the very highest quality and giving you peace of mind that you've got a professional and trustworthy team at your side.</p>
  <a class="btn">Learn More <i></i></a>
</section>
<section class="testimonials">
  <h2 class="section-title">Client Testimonials</h2>
  <svg class="carousel-arrow" style="left:66px" width="14" height="20" viewBox="0 0 14 20"><path d="M10 3L4 10l6 7" fill="none" stroke="#fff" stroke-width="2.5"/></svg>
  <svg class="carousel-arrow" style="right:66px" width="14" height="20" viewBox="0 0 14 20"><path d="M4 3l6 7-6 7" fill="none" stroke="#fff" stroke-width="2.5"/></svg>
  <div class="review" style="left:162px;top:221px;width:241px;height:193px">
    <div class="avatar" role="img" aria-label="Client portrait" style="top:-28px;width:64px;height:64px"></div>
    <h4 style="margin-top:60px;font-size:14px">Clara Vendell</h4>
    <div class="lead" style="font-size:14px;margin-top:10px">Lorem ipsum dolor amet</div>
    <div class="body" style="font-size:13px;line-height:17px;margin:12px 20px 0">Lorem ipsum consectetur adipiscing elit, sed do eiusmod tempor labore dolore magna.</div>
  </div>
  <div class="review" style="left:452px;top:186px;width:295px;height:236px">
    <div class="avatar" role="img" aria-label="Client portrait" style="top:-38px;width:84px;height:84px"></div>
    <h4 style="margin-top:66px;font-size:17px">Owen Marsh</h4>
    <div class="lead" style="font-size:16px;margin-top:14px">Lorem ipsum dolor amet</div>
    <div class="body" style="font-size:15px;line-height:21px;margin:14px 22px 0">Lorem ipsum dolor consectetur adipiscing elit, sed do eiusmod tempor incididunt ut labore dolore magna aliqua.</div>
  </div>
  <div class="review" style="left:797px;top:222px;width:241px;height:193px">
    <div class="avatar" role="img" aria-label="Client portrait" style="top:-28px;width:64px;height:64px"></div>
    <h4 style="margin-top:60px;font-size:14px">Rafe Dunmore</h4>
    <div class="lead" style="font-size:14px;margin-top:10px">Lorem ipsum dolor amet</div>
    <div class="body" style="font-size:13px;line-height:17px;margin:12px 20px 0">Lorem ipsum consectetur adipiscing elit, sed do eiusmod tempor labore dolore magna.</div>
  </div>
</section>
<section class="services">
  <h2 class="section-title">Our Services</h2>
  <div class="service-row">
    <div class="service" style="left:125px">
      <svg viewBox="0 0 120 120"><circle cx="78" cy="30" r="24" fill="#0d5cb6"/><rect x="10" y="64" width="20" height="46" fill="#0d5cb6"/><path d="M34 72h30l30-10c8-2 10 8 4 12l-30 26H34z" fill="#0d5cb6"/></svg>
      <h3>BASIC OFFERING</h3>
      <ul><li>Lower cost per month</li><li>Slower release schedule</li><li>Limited support hours</li></ul>
      <a class="more">Read More ›</a>
    </div>
    <div class="service" style="left:450px">
      <svg viewBox="0 0 120 120"><circle cx="90" cy="26" r="12" fill="none" stroke="#0d5cb6" stroke-width="5"/><path d="M36 8v30M26 10v14h20V10" fill="none" stroke="#0d5cb6" stroke-width="6"/><rect x="42" y="44" width="46" height="40" fill="#0d5cb6"/><rect x="10" y="80" width="18" height="30" fill="#0d5cb6"/><path d="M32 86h40l30-10v14l-30 18H32z" fill="#0d5cb6"/></svg>
      <h3>FULL SERVICE OFFERING</h3>
      <ul><li>Mid-range cost per month</li><li>Releases every 1.5 - 2 months</li><li>Client can help request</li></ul>
      <a class="more">Read More ›</a>
    </div>
    <div class="service" style="left:777px">
      <svg viewBox="0 0 120 120"><circle cx="30" cy="30" r="10" fill="#0d5cb6"/><circle cx="60" cy="18" r="10" fill="#0d5cb6"/><circle cx="90" cy="30" r="10" fill="#0d5cb6"/><path d="M36 50h48l-6 22H42z" fill="#0d5cb6"/><path d="M10 80h40l40-8c10 0 12 10 4 14l-30 22H24z" fill="#0d5cb6"/></svg>
      <h3>PREMIUM SERVICE</h3>
      <ul><li>Higher cost per month</li><li>Priority 24/7 support</li><li>Dedicated development lead</li></ul>
      <a class="more">Read More ›</a>
    </div>
  </div>
</section>
<section class="promo">
  <h2 class="section-title">Lorem Ipsum Dolor</h2>
  <p>Lorem ipsum dolor sit amet, consectetur adipiscing elit, sed do eiusmod tempor incididunt ut labore et dolore magna aliqua. Ut enim ad minim veniam, quis nostrud exercitation ullamco laboris nisi ut aliquip ex ea commodo consequat. Duis aute irure dolor in reprehenderit in voluptate velit esse cillum dolore fugiat nulla pariatur. Excepteur sint occaecat cupidatat non proident, sunt in culpa qui officia</p>
  <a class="btn">Schedule Free Consultation <i></i></a>
</section>
<footer class="footer">
  <div class="footer-edge"></div>
  <div class="footer-body">
    <div class="footer-brand"><div class="brand-mark"></div><div class="brand-name">Ledgerwise<br>Forge</div></div>
    <p class="footer-about">Ledgerwise Forge adds professionalism to cryptocurrency development.</p>
    <div class="footer-col" style="left:442px"><h5>Quicklinks</h5><ul><li>Services</li><li>Ledgerwise Forge Method</li><li>Testimonials</li><li>Blog</li><li>About Us</li></ul></div>
    <div class="footer-col" style="left:712px"><h5>Qtherlinks</h5><ul><li>Blog</li><li>privacy</li><li>Services</li><li>Team</li></ul></div>
    <div class="newsletter">
      <h5>Get our Newsletter</h5>
      <div class="field">Enter News</div>
      <a class="btn">Subscribe</a>
      <div class="social"><span></span><span></span><span></span><span></span><span></span></div>
    </div>
    <div class="footer-rule"></div>
    <div class="copyright">©Copyrights 2021 &nbsp; Ledgerwise Forge &nbsp;| &nbsp; All Rights Reserved &nbsp;|</div>
  </div>
</footer>
</body>
</html>
```